KDWB Business Card

Looking for a business card design to incorporate our branding. We want to only use the colors listing in the Branding Package (attached).
Updates

Target Market(s)

People who need their phone or device fixed.

Industry/Entity Type

Electronics

Contact Information for Business Card

Please use:

Brightwick Gadget Clinic LLC
4810 E Harlow Ridge Rd
Suite 417
San Antonio, TX 78163

Marcus Delgrove, Store Manager

(210) 555-0147

Requirements
Must have
• Must include the colors that are contained within the Branding Package PDF file.

```html
<!DOCTYPE html>
<html lang="en">
<head>
<meta charset="utf-8">
<title>Brightwick Gadget Clinic – Business Card</title>
<link href="https://fonts.googleapis.com/css2?family=Arimo:wght@400&display=swap" rel="stylesheet">
<style>
  :root {
    --backdrop: #c6c6c8;
    --charcoal: #525355;
    --band-light: #f4f4f4;
    --band-grey: #bdbdbd;
    --orange: #e8542a;
    --ink: #1e1e1e;
    --ink-soft: #2f2f2f;
    --card-white: #f5f5f5;
  }
  * { margin: 0; padding: 0; box-sizing: border-box; }
  html, body { width: 1200px; height: 1200px; overflow: hidden; }
  body {
    background: var(--backdrop);
    font-family: "Arimo", Arial, sans-serif;
    position: relative;
  }
  .card {
    position: absolute;
    border-radius: 10px;
    overflow: hidden;
    box-shadow: 0 6px 14px rgba(0,0,0,0.25);
  }
  .card-front { left: 262px; top: 148px; width: 672px; height: 400px; background: var(--band-grey); }
  .card-back  { left: 256px; top: 628px; width: 684px; height: 398px; background: var(--card-white); }

  .brand-band {
    height: 184px;
    background: var(--charcoal);
    display: flex; align-items: center; justify-content: center;
  }
  .brand-mark { display: flex; align-items: center; gap: 16px; }
  .brand-square {
    width: 72px; height: 72px; border-radius: 10px;
    background: var(--orange);
  }
  .brand-name { color: var(--orange); font-size: 34px; line-height: 1.1; }

  .name-band {
    height: 63px;
    background: var(--band-light);
    text-align: center;
    padding-top: 3px;
  }
  .person-name { font-size: 29px; color: var(--ink); letter-spacing: -0.3px; line-height: 1.1; }
  .person-title { font-size: 18px; color: var(--orange); line-height: 1.2; }

  .contact-block {
    text-align: center;
    color: var(--ink-soft);
    font-size: 16.5px;
    letter-spacing: 0.6px;
    padding-top: 24px;
  }
  .contact-phone { margin-bottom: 22px; }
  .contact-line { line-height: 26px; }

  .photo-wash {
    position: absolute; inset: 0;
    background: linear-gradient(160deg, #f3f3f4 0%, #e7e8ee 40%, #eae9ec 70%, #f4f4f4 100%);
  }
  .back-mark {
    position: absolute; inset: 0;
    display: flex; align-items: center; justify-content: center;
  }
  .back-mark .brand-square { width: 92px; height: 92px; border-radius: 12px; }
  .back-mark .brand-name { font-size: 44px; }
</style>
</head>
<body>
  <section class="card card-front">
    <div class="brand-band">
      <div class="brand-mark">
        <div class="brand-square"></div>
        <div class="brand-name">Brightwick Gadget Clinic</div>
      </div>
    </div>
    <div class="name-band">
      <div class="person-name">Marcus Delgrove</div>
      <div class="person-title">Store Manager</div>
    </div>
    <div class="contact-block">
      <div class="contact-phone">(210) 555-0147</div>
      <div class="contact-line">marcus@brightwickclinic.com</div>
      <div class="contact-line">www.brightwickclinic.com</div>
      <div class="contact-line">4810 E Harlow Ridge Rd, Suite 417, San Antonio, TX 78163</div>
    </div>
  </section>

  <section class="card card-back">
    <div class="photo-wash" role="img" aria-label="Faded photo of hands repairing a smartphone on a blue mat"></div>
    <div class="back-mark">
      <div class="brand-mark">
        <div class="brand-square"></div>
        <div class="brand-name">Brightwick Gadget Clinic</div>
      </div>
    </div>
  </section>
</body>
</html>
```